BOLD & MINIMALIST DESIGN NEEDED

We want a very bold but minimalistic business card design that is impactful and utilizes both sides of the business card. Our current logo is included for your use.

We want bold fonts and good use of negative space. We don't want the logo to overpower the design.

Target Market(s)

Professionals who are building new commercial buildings.

Industry/Entity Type

Construction

Contact Information for Business Card

Name, Title, email, office phone, cell phone, website

Font styles to use
Serif
Sans Serif

Requirements
Must have
• Bold design!

```html
<!DOCTYPE html>
<html lang="en">
<head>
<meta charset="utf-8">
<title>Stonecrest Business Card</title>
<link rel="stylesheet" href="https://fonts.googleapis.com/css2?family=Poppins:wght@300;400;500;600&display=swap">
<style>
  :root {
    --backdrop: #2a2a2a;
    --card-dark: #252526;
    --card-light: #efefef;
    --ink: #1e1e1e;
    --accent: #7ab51d;
    --muted-light: #bdbdbd;
    --mark-grey: #4a4a4c;
  }
  * { box-sizing: border-box; margin: 0; padding: 0; }
  html, body {
    width: 1200px;
    height: 576px;
    overflow: hidden;
    background: var(--backdrop);
    font-family: "Poppins", sans-serif;
  }
  .stage {
    position: relative;
    width: 1200px;
    height: 576px;
  }
  .card {
    position: absolute;
    top: 138px;
    width: 484px;
    height: 292px;
    border-radius: 8px;
  }
  .card--front {
    left: 102px;
    background: var(--card-dark);
  }
  .card--back {
    left: 596px;
    background: var(--card-light);
  }
  .front-wordmark {
    position: absolute;
    left: 0;
    right: 0;
    top: 100px;
    text-align: center;
    font-size: 48px;
    font-weight: 600;
    letter-spacing: 2px;
    color: var(--mark-grey);
  }
  .front-website {
    position: absolute;
    left: 0;
    right: 0;
    top: 251px;
    text-align: center;
    font-size: 13px;
    font-weight: 300;
    letter-spacing: 6px;
    color: var(--muted-light);
  }
  .person {
    position: absolute;
    right: 30px;
    top: 28px;
    text-align: right;
  }
  .person__name {
    font-size: 21px;
    font-weight: 500;
    color: var(--accent);
    line-height: 1.2;
  }
  .person__title {
    font-size: 11px;
    font-weight: 400;
    color: var(--ink);
    margin-top: 2px;
  }
  .brand {
    position: absolute;
    left: 32px;
    top: 226px;
    display: flex;
    align-items: center;
    gap: 8px;
  }
  .brand__square {
    width: 14px;
    height: 14px;
    background: var(--ink);
  }
  .brand__name {
    font-size: 21px;
    font-weight: 500;
    color: var(--ink);
    line-height: 1;
  }
  .contacts {
    position: absolute;
    right: 30px;
    top: 214px;
    list-style: none;
    text-align: right;
  }
  .contacts li {
    display: flex;
    justify-content: flex-end;
    align-items: center;
    gap: 6px;
    font-size: 11.5px;
    color: var(--ink);
    line-height: 17px;
  }
  .contacts svg {
    width: 10px;
    height: 10px;
    fill: var(--accent);
  }
</style>
</head>
<body>
<main class="stage">
  <section class="card card--front" aria-label="Card front">
    <div class="front-wordmark">STONECREST</div>
    <div class="front-website">www.stonecrest.com</div>
  </section>

  <section class="card card--back" aria-label="Card back">
    <div class="person">
      <div class="person__name">Daniel Reyes</div>
      <div class="person__title">Director</div>
    </div>

    <div class="brand">
      <span class="brand__square"></span>
      <span class="brand__name">Stonecrest</span>
    </div>

    <ul class="contacts">
      <li>555-014-0192
        <svg viewBox="0 0 10 10" aria-hidden="true"><path d="M1 3.5 C1 1.5 9 1.5 9 3.5 L9 4.5 L7 4.5 L7 3.5 L3 3.5 L3 4.5 L1 4.5 Z M2.5 5 L7.5 5 L9 9 L1 9 Z"/></svg>
      </li>
      <li>daniel@stonecrest.com
        <svg viewBox="0 0 10 10" aria-hidden="true"><path d="M0.5 2 L9.5 2 L5 5.5 Z M0.5 3 L5 6.5 L9.5 3 L9.5 8.5 L0.5 8.5 Z"/></svg>
      </li>
      <li>www.stonecrest.com
        <svg viewBox="0 0 10 10" aria-hidden="true"><circle cx="5" cy="5" r="4.5"/></svg>
      </li>
    </ul>
  </section>
</main>
</body>
</html>
```